Fresh new and cool frozen burger box! Come be a part of an amazing project!

Crust Drums and Melts restaurant is expanding into the frozen foods market!
please check out our website to understand the vibe of the company
https://crumbvale.ca
this is a line of premium Halal meat, we want to stress our top-notch quality.
we like the orange colours so see what you can do with them. (maybe white and orange combo)
you have lots of creative freedom here, feel free to use the burger photo I am attaching or any image off the website.
logo should be nice and visible.
we want this packaging to really stand out and be special.
Come be a part of an amazing project!
Muslim Flails, looking of a quality meat burger. mostly already familiar with our brand
Frozen food

```html
<!DOCTYPE html>
<html lang="en">
<head>
<meta charset="utf-8">
<title>Crumbvale – Frozen Burger Box Dieline</title>
<link href="https://fonts.googleapis.com/css2?family=Anton&family=Roboto+Condensed:wght@400;700;900&display=swap" rel="stylesheet">
<style>
  :root {
    --stage: #cbcbcb;
    --orange: #f29a1c;
    --orange-deep: #e5820f;
    --orange-light: #f6ab33;
    --black: #141414;
    --tray: #1e1e1e;
    --white: #ffffff;
    --paper: #eeeeee;
    --ink: #2a2a2a;
    --red: #d8231b;
    --photo-light: #d9a265;
    --photo-dark: #8a5a32;
  }
  * { margin: 0; padding: 0; box-sizing: border-box; }
  html, body { width: 1200px; height: 724px; overflow: hidden; }
  body { background: var(--stage); position: relative; font-family: "Roboto Condensed", Arial, sans-serif; }

  .panel { position: absolute; overflow: hidden; box-shadow: 0 6px 18px rgba(0,0,0,.18); }

  .photo-slot { position: absolute; border-radius: 18px;
    background: radial-gradient(ellipse at 50% 40%, var(--photo-light) 0%, var(--photo-dark) 100%); }

  /* Lid top */
  .lid { left: 60px; top: 80px; width: 460px; height: 470px; background: linear-gradient(160deg, var(--orange-light), var(--orange-deep)); }
  .lid__band { position: absolute; inset: 0; }
  .lid__brand { position: absolute; left: 0; right: 0; top: 44px; display: flex; flex-direction: column; align-items: center; }
  .lid__photo { left: 70px; top: 150px; width: 320px; height: 170px; }

  /* Front face */
  .front { left: 560px; top: 80px; width: 580px; height: 250px; background: linear-gradient(120deg, var(--orange-deep), var(--orange-light)); }
  .front__brand { position: absolute; left: 0; right: 0; top: 48px; display: flex; flex-direction: column; align-items: center; }
  .tray { position: absolute; left: 560px; top: 330px; width: 580px; height: 44px; background: var(--tray); }

  /* Side face */
  .side { left: 560px; top: 404px; width: 580px; height: 240px; background: var(--paper); }
  .side__photo { left: 30px; top: 40px; width: 200px; height: 160px; }
  .side__copy { position: absolute; left: 260px; top: 34px; width: 290px; }
  .side__text { margin-top: 12px; font-size: 14px; line-height: 1.35; color: var(--ink); font-weight: 700; }

  /* Brand lockup */
  .brand { display: flex; align-items: center; gap: 12px; }
  .brand__dot { border-radius: 50%; background: var(--white); flex: none; }
  .brand__name { font-family: "Anton", Impact, sans-serif; color: var(--white); letter-spacing: 1px; line-height: 1; }
  .tagline { font-weight: 900; letter-spacing: .5px; color: var(--black); }
  .tagline .sep { color: var(--red); padding: 0 6px; }

  .brand--lg .brand__dot { width: 54px; height: 54px; }
  .brand--lg .brand__name { font-size: 86px; }
  .tagline--lg { font-size: 34px; margin-top: 6px; }

  .brand--sm .brand__dot { width: 28px; height: 28px; }
  .brand--sm .brand__name { font-size: 42px; }
  .tagline--sm { font-size: 18px; margin-top: 4px; color: var(--white); }

  .brand--side .brand__dot { width: 28px; height: 28px; background: var(--red); }
  .brand--side .brand__name { font-size: 44px; color: var(--red); }
  .tagline--side { font-size: 19px; margin-top: 2px; }
</style>
</head>
<body>

  <section class="panel lid">
    <svg class="lid__band" width="460" height="470" viewBox="0 0 460 470">
      <line x1="80" y1="0" x2="80" y2="470" stroke="#141414" stroke-width="6"/>
      <line x1="380" y1="0" x2="380" y2="470" stroke="#141414" stroke-width="6"/>
      <path d="M95 0 H365 V330 Q365 440 230 440 Q95 440 95 330 Z" fill="#141414"/>
    </svg>
    <div class="lid__brand">
      <div class="brand brand--sm"><span class="brand__dot"></span><span class="brand__name">CRUMBVALE</span></div>
      <p class="tagline tagline--sm">Crust<span class="sep">•</span>Drums<span class="sep">•</span>Melts</p>
    </div>
    <div class="photo-slot lid__photo" role="img" aria-label="Photo of a halal beef burger with bacon, cheese, tomato and lettuce on a sesame bun"></div>
  </section>

  <section class="panel front">
    <div class="front__brand">
      <div class="brand brand--lg"><span class="brand__dot"></span><span class="brand__name">CRUMBVALE</span></div>
      <p class="tagline tagline--lg">Crust<span class="sep">•</span>Drums<span class="sep">•</span>Melts</p>
    </div>
  </section>
  <div class="tray" role="img" aria-label="Black tray base with faint food line pattern"></div>

  <section class="panel side">
    <div class="photo-slot side__photo" role="img" aria-label="Photo of a stacked burger with tomato, bacon, cheese and lettuce"></div>
    <div class="side__copy">
      <div class="brand brand--side"><span class="brand__dot"></span><span class="brand__name">CRUMBVALE</span></div>
      <p class="tagline tagline--side">Crust<span class="sep">•</span>Drums<span class="sep">•</span>Melts</p>
      <p class="side__text">Premium halal beef patties, flame grilled and frozen fresh to lock in juicy flavour. Heat, stack and enjoy a restaurant quality burger at home. Made with hand picked cuts, no fillers and our signature seasoning blend for a bold, clean taste.</p>
    </div>
  </section>

</body>
</html>
```